Redesign to improve branding visibility and product messaging

Update the logo using the new logo provided attached.
Then, improve product messaging on the packaging, however leaving the colours, general blurbs, and the fruit/nut image outlines as they are (but open to make it simpler).
Please review photos Stockist 1" to 5" and recommend the new style for:
1 Energy Ball Bag
1 Energy Ball Inner Box
1 Cereal Bag
Key features:
1. Allow more transparent window to show more of the product inside.
2. Strong brand presence and clear nutritional call outs - keep in mind we display our products on supermarket shelves.
3. Product Messaging:
- 1st priority: Product Name
- 2nd priority: Nutritional call outs (All natural, GF, Vegan, High Fibre, No added sugar, etc.). This info is available in the current packaging and more info on the website.
- 3rd priority: Ingredients on front cover (example: 7 ingredients only: x1, x2, x3, x4, x5, x6, x7.)
- 4th priority: Locally Made by a nutritionist.
- 5th priority: Sugar content in the nutritional panel to say: From Healthy Natural Sources
Tips:
1. Use Style 1 as benchmark.
2. Use the other image references as follows:
Style 2 and 5 = Try do something similar for the energy ball bags.
Style 4 = Maybe add the line up of other flavours on the back or the side of the packaging for the energy ball box and the cereal bags.
Style 7 = Do something similar with regards to the use of real imagery on the packaging as if you can pick out the product right of the packaging. Note also how they list the ingredients on the front of packaging.
Style 8 = Do something similar - be proud about the real ingredients used.
Style 9 = An example of how much transparent area we can do, please suggest a nice unique transparent shape.
Style 10 = copy the way it communicates the health benefits very clearly.

```html
<!DOCTYPE html>
<html lang="en">
<head>
<meta charset="utf-8">
<title>Well Pantry – Apricot &amp; Coconut Energy Balls Pack</title>
<link href="https://fonts.googleapis.com/css2?family=Montserrat:wght@400;500;600;700;800&family=Allura&display=swap" rel="stylesheet">
<style>
  :root {
    --bg: #f1f1f1;
    --bag: #e6a9a4;
    --bag-light: #efc1bc;
    --bag-deep: #d9938e;
    --ink: #1d1d1d;
    --ink-soft: #4a3a3a;
    --white: #ffffff;
    --cream: #f3e6d6;
    --apricot: #e2b27c;
  }
  * { margin: 0; padding: 0; box-sizing: border-box; }
  html, body { width: 856px; height: 1200px; overflow: hidden; background: var(--bg); }
  body { font-family: "Montserrat", sans-serif; }
  .canvas { position: relative; width: 856px; height: 1200px; }

  .bag {
    position: absolute; left: 45px; width: 764px; height: 498px;
    background: linear-gradient(180deg, var(--bag-light) 0%, var(--bag) 40%, var(--bag) 100%);
    border-radius: 6px; overflow: hidden;
  }
  .bag--back { top: 40px; }
  .bag--front { top: 635px; }
  .bag::before, .bag::after {
    content: ""; position: absolute; top: 0; bottom: 0; width: 26px; z-index: 5;
    background: repeating-linear-gradient(90deg, var(--bag-deep) 0 2px, var(--bag-light) 2px 5px);
    opacity: .55;
  }
  .bag::before { left: 0; }
  .bag::after { right: 0; }
  .bag__shapes { position: absolute; inset: 0; }

  .text { position: absolute; z-index: 3; }

  /* back panel */
  .benefits-title { left: 267px; top: 57px; font-size: 20.5px; font-weight: 800; color: var(--ink); letter-spacing: .2px; white-space: nowrap; }
  .blurb-box { position: absolute; left: 198px; top: 89px; width: 482px; height: 120px; border: 1px solid var(--ink-soft); border-radius: 6px; background: rgba(255,255,255,.1); z-index: 2; }
  .blurb { left: 267px; top: 111px; width: 400px; font-size: 10.6px; line-height: 15px; font-weight: 600; color: var(--white); text-transform: uppercase; }
  .nutrition-panel { position: absolute; left: 66px; top: 293px; width: 189px; height: 160px; border: 1.2px solid var(--ink-soft); border-radius: 9px; z-index: 2; }
  .nutrition-panel__title { position: absolute; top: 8px; width: 100%; text-align: center; font-size: 10.5px; font-weight: 700; color: var(--ink); }
  .nutrition-panel__rows { position: absolute; left: 21px; right: 17px; top: 49px; list-style: none; }
  .nutrition-panel__rows li { display: flex; justify-content: space-between; font-size: 6.5px; line-height: 10.4px; font-weight: 600; color: var(--white); text-transform: uppercase; }
  .kitchen { left: 291px; top: 332px; color: var(--ink-soft); font-size: 8px; line-height: 10.6px; }
  .kitchen strong { display: block; font-weight: 700; color: var(--ink); font-size: 8.2px; }
  .storage { left: 293px; top: 400px; }
  .storage h3 { font-size: 11px; font-weight: 700; color: var(--ink); margin-bottom: 5px; }
  .storage p { font-size: 7.5px; line-height: 10px; font-weight: 600; color: var(--white); }

  /* front panel */
  .brand { left: 0; width: 806px; top: 150px; text-align: center; font-size: 14px; font-weight: 600; letter-spacing: 3px; color: var(--white); }
  .product-name { left: 0; width: 772px; top: 196px; text-align: center; font-size: 33px; font-weight: 800; color: var(--ink); letter-spacing: .3px; }
  .product-type { left: 0; width: 780px; top: 214px; text-align: center; font-family: "Allura", cursive; font-size: 58px; color: var(--white); z-index: 4; }
  .claim-label { top: 348px; width: 64px; text-align: center; font-size: 6.8px; line-height: 8.5px; font-weight: 700; color: var(--white); }
  .highlights { left: 78px; top: 322px; }
  .highlights h3 { font-size: 10.5px; font-weight: 800; color: var(--ink-soft); line-height: 10px; }
  .highlights h4 { font-size: 16.5px; font-weight: 800; color: var(--ink-soft); line-height: 17px; margin-bottom: 2px; }
  .highlights li { font-size: 7.4px; line-height: 9.5px; font-weight: 500; color: var(--white); list-style: none; }
  .ingredients { left: 0; width: 816px; top: 401px; text-align: center; }
  .ingredients h3 { font-size: 12px; font-weight: 800; color: var(--white); margin-bottom: 6px; }
  .ingredients p { font-size: 8.2px; line-height: 9.6px; font-weight: 500; color: var(--ink-soft); text-transform: uppercase; }
</style>
</head>
<body>
<main class="canvas">

  <!-- Back of pack -->
  <section class="bag bag--back" aria-label="Back of pack">
    <svg class="bag__shapes" width="764" height="498" viewBox="0 0 764 498">
      <defs>
        <radialGradient id="ballTone" cx="40%" cy="38%" r="65%">
          <stop offset="0%" stop-color="#f7efe4"/>
          <stop offset="65%" stop-color="#ecd7bd"/>
          <stop offset="100%" stop-color="#d9b185"/>
        </radialGradient>
      </defs>
      <rect x="0" y="240" width="764" height="14" fill="#efbcb7" opacity=".6"/>
      <ellipse role="img" aria-label="Line drawing of an apricot and almond" cx="560" cy="370" rx="150" ry="125" fill="#f2c7c3" opacity=".55"/>
      <circle role="img" aria-label="Photo of a coconut-rolled energy ball" cx="134" cy="126" r="108" fill="url(#ballTone)"/>
      <circle role="img" aria-label="Photo of a coconut-rolled energy ball" cx="419" cy="239" r="66" fill="url(#ballTone)"/>
      <circle role="img" aria-label="Photo of a coconut-rolled energy ball" cx="682" cy="303" r="97" fill="url(#ballTone)"/>
    </svg>

    <h2 class="text benefits-title">DIGESTIVE + ENERGY + ANTIOXIDANT</h2>
    <div class="blurb-box"></div>
    <p class="text blurb">Sweet, chewy &amp; delicious, our apricot &amp; coconut energy ball is full of fibre and contains vitamin A, potassium to support electrolyte balance, magnesium to help with muscle &amp; nerve function, and iron.</p>

    <div class="nutrition-panel">
      <h3 class="nutrition-panel__title">NUTRITION PANEL</h3>
      <ul class="nutrition-panel__rows">
        <li><span>Energy</span><span>1G</span></li>
        <li><span>Protein</span><span>1G</span></li>
        <li><span>Fat - Total</span><span>1G</span></li>
        <li><span>Fat - Saturated</span><span>1G</span></li>
        <li><span>Carbohydrates</span><span>1G</span></li>
        <li><span>Total</span><span>1G</span></li>
        <li><span>Sugars from natural sources</span><span>1G</span></li>
        <li><span>Dietary Fibre</span><span>1G</span></li>
        <li><span>Sodium</span><span>1G</span></li>
      </ul>
    </div>

    <p class="text kitchen"><strong>JOIN US IN THE KITCHEN</strong>View more healthy recipes<br>#WELLPANTRYKITCHEN<br>@WELLPANTRY</p>

    <div class="text storage">
      <h3>STORAGE</h3>
      <p>Store in a cool dry place.<br>Reseal after opening.</p>
    </div>
  </section>

  <!-- Front of pack -->
  <section class="bag bag--front" aria-label="Front of pack">
    <svg class="bag__shapes" width="764" height="498" viewBox="0 0 764 498">
      <defs>
        <radialGradient id="ballToneFront" cx="40%" cy="38%" r="65%">
          <stop offset="0%" stop-color="#f7efe4"/>
          <stop offset="65%" stop-color="#ecd7bd"/>
          <stop offset="100%" stop-color="#d9b185"/>
        </radialGradient>
        <radialGradient id="windowTone" cx="50%" cy="50%" r="60%">
          <stop offset="0%" stop-color="#e9b7a8"/>
          <stop offset="100%" stop-color="#dca09b"/>
        </radialGradient>
      </defs>
      <circle role="img" aria-label="Line drawing of a coconut with energy balls behind" cx="398" cy="210" r="158" fill="url(#windowTone)" opacity=".75"/>
      <circle role="img" aria-label="Line drawing of an apricot with an energy ball behind" cx="645" cy="340" r="120" fill="url(#windowTone)" opacity=".6"/>
      <circle role="img" aria-label="Photo of a coconut-rolled energy ball" cx="124" cy="103" r="111" fill="url(#ballToneFront)"/>
      <circle role="img" aria-label="Photo of a coconut-rolled energy ball" cx="669" cy="105" r="92" fill="url(#ballToneFront)"/>
      <ellipse role="img" aria-label="Photo of a cluster of energy balls" cx="113" cy="452" rx="72" ry="62" fill="url(#ballToneFront)"/>
      <circle role="img" aria-label="Photo of a coconut-rolled energy ball" cx="258" cy="478" r="68" fill="url(#ballToneFront)"/>

      <!-- locally made badge -->
      <defs>
        <path id="badgeArc" d="M108,269 m-36,0 a36,36 0 1,1 72,0 a36,36 0 1,1 -72,0"/>
      </defs>
      <text font-family="Montserrat, sans-serif" font-size="7.6" font-weight="600" fill="#ffffff" letter-spacing="1.4">
        <textPath href="#badgeArc" startOffset="2%">LOCALLY MADE BY A NUTRITIONIST</textPath>
      </text>
      <path d="M108,282 C96,272 92,266 97,260 C101,256 106,258 108,262 C110,258 115,256 119,260 C124,266 120,272 108,282 Z" fill="#4a4a4a"/>

      <!-- claim icons -->
      <g fill="none" stroke="#ffffff" stroke-width="1.2">
        <circle cx="322" cy="319" r="25"/>
        <circle cx="387" cy="319" r="25"/>
        <circle cx="450" cy="316" r="25"/>
        <rect x="314" y="311" width="16" height="16" rx="1"/>
        <line x1="306" y1="303" x2="338" y2="335"/>
        <line x1="387" y1="305" x2="387" y2="334"/>
        <ellipse cx="382" cy="313" rx="4" ry="6"/>
        <ellipse cx="392" cy="313" rx="4" ry="6"/>
        <line x1="371" y1="303" x2="403" y2="335"/>
        <rect x="439" y="316" width="22" height="11" rx="1"/>
        <line x1="439" y1="321" x2="461" y2="321"/>
        <path d="M443,316 q-2,-8 3,-10 M450,316 q0,-9 4,-10 M456,316 q3,-7 6,-7"/>
      </g>
    </svg>

    <p class="text brand">WELL PANTRY</p>
    <h1 class="text product-name">APRICOT &amp; COCONUT</h1>
    <p class="text product-type">Energy balls</p>

    <p class="text claim-label" style="left:290px">NO ADDED<br>SUGAR</p>
    <p class="text claim-label" style="left:355px">GLUTEN FREE</p>
    <p class="text claim-label" style="left:418px">VEGAN</p>

    <div class="text highlights">
      <h3>NUTRITION</h3>
      <h4>HIGHLIGHTS</h4>
      <ul>
        <li>• HIGH FIBRE - DIGESTIVE SUPPORT</li>
        <li>• HEALTHY FATS - SUSTAINED ENERGY</li>
        <li>• ANTIOXIDANTS - IMMUNITY</li>
      </ul>
    </div>

    <div class="text ingredients">
      <h3>6 INGREDIENTS</h3>
      <p>Dried apricot - almond meal - maple syrup<br>coconut oil - desiccated coconut<br>- vanilla extract</p>
    </div>
  </section>

</main>
</body>
</html>
```